Concise,Good colour matching,Good looks design for "HERD SCAN QUICK ASSAY FOR LIVESTOCK"

Product Positioning: Affordable test for Large Animals (Livestock/Veterinary Use)
Product Name: HERD SCAN Quick Assay Kit (for large animals, e.g., cattle, horses, swine,Avian,sheep).

2. Packaging Requirements

A. Visual Design
Color Scheme:
Green/Blue/Orange/Yellow/Red/Gray/White(chose 2~4 colors)

Mandatory Info:
Brand logo ("HERD SCAN")

Target Market(s)

Southeast Asia, Africa, Middle East, South America

Industry/Entity Type

Veterinary diagnostic for LIVESTOCK

Colors

Designer to choose colors to be used in the design.

Requirements
Nice to have
• Concise,Good colour matching,Good looks

```html
<!DOCTYPE html>
<html lang="en">
<head>
<meta charset="utf-8">
<title>Herd Scan Quick Assay – Packaging Panels</title>
<link href="https://fonts.googleapis.com/css2?family=Fraunces:opsz,wght@9..144,700;9..144,800&family=Montserrat:wght@400;500;600&family=Allura&display=swap" rel="stylesheet">
<style>
  :root {
    --orange: #fc5a06;
    --orange-light: #ff8a1c;
    --amber: #ffa21a;
    --yellow: #ffdd00;
    --yellow-text: #ffe81a;
    --white: #ffffff;
    --ink: #1e1a16;
    --page: #f3f3f3;
    --hide-brown: #8a3a14;
    --hide-cream: #e9dcc8;
  }
  * { margin: 0; padding: 0; box-sizing: border-box; }
  html, body { width: 1200px; height: 470px; overflow: hidden; background: var(--page); }
  .canvas { position: relative; width: 1200px; height: 470px; }

  .panel { position: absolute; overflow: hidden; }

  /* Front panel */
  .front { left: 166px; top: 20px; width: 574px; height: 430px; background: var(--orange); }
  .front-arc { position: absolute; left: 0; top: 0; }
  .brand-word {
    font-family: "Montserrat", sans-serif; font-weight: 600; letter-spacing: -0.5px; white-space: nowrap;
  }
  .front .brand-word { position: absolute; left: 25px; top: 48px; font-size: 27px; color: var(--white); }
  .headline {
    position: absolute; left: 29px; top: 122px;
    font-family: "Fraunces", serif; font-weight: 800; line-height: 47px; font-size: 41px; color: var(--white);
  }
  .headline .accent { color: var(--yellow-text); }
  .headline .script {
    font-family: "Allura", cursive; font-weight: 400; font-size: 52px; color: var(--white); margin-right: 6px;
  }
  .headline .indent { padding-left: 24px; }
  .front-sub {
    position: absolute; left: 25px; top: 346px;
    font-family: "Montserrat", sans-serif; font-weight: 400; font-size: 15.5px; line-height: 20px; color: var(--white);
  }
  .herd-photo {
    position: absolute; left: 282px; top: 102px; width: 274px; height: 328px;
    border-radius: 46% 40% 0 0 / 30% 26% 0 0;
    background: linear-gradient(160deg, var(--hide-brown) 0%, #a4481c 55%, var(--hide-cream) 100%);
  }

  /* Side panels */
  .side { left: 750px; width: 284px; }
  .logo-panel { top: 20px; height: 113px; background: var(--white); }
  .logo-panel .brand-word {
    position: absolute; left: 0; right: 0; top: 36px; text-align: center; font-size: 36px; color: var(--orange);
  }

  .info-panel { top: 140px; height: 153px; background: var(--yellow); }
  .info-title {
    position: absolute; left: 16px; top: 14px;
    font-family: "Fraunces", serif; font-weight: 800; font-size: 13px; line-height: 16px; color: var(--ink);
  }
  .info-copy {
    font-family: "Montserrat", sans-serif; font-weight: 500; font-size: 6.3px; line-height: 8px; color: var(--ink);
  }
  .info-panel .speed { position: absolute; left: 16px; top: 54px; width: 100px; }
  .info-panel .note {
    position: absolute; left: 15px; top: 98px; width: 110px; height: 36px;
    background: var(--white); padding: 4px 5px;
  }
  .kid-photo {
    position: absolute; left: 113px; top: 27px; width: 44px; height: 95px;
    border-radius: 45% 45% 30% 30%;
    background: linear-gradient(180deg, #f4ede2 0%, #cfc3b0 100%);
  }
  .value-box {
    position: absolute; left: 157px; top: 15px; width: 110px; height: 119px;
    background: var(--orange); padding: 8px 8px;
  }
  .value-title { font-family: "Fraunces", serif; font-weight: 800; font-size: 13px; color: var(--yellow-text); }
  .value-box .info-copy { color: var(--white); margin-top: 3px; }
  .value-box .brand-word { position: absolute; left: 10px; bottom: 6px; font-size: 16px; color: var(--amber); }

  .spec-panel { top: 300px; height: 150px; background: var(--white); }
  .spec {
    position: absolute; left: 19px; top: 52px;
    font-family: "Montserrat", sans-serif; font-weight: 400; font-size: 7.6px; line-height: 10px; color: var(--ink);
  }
  .spec-name { font-family: "Fraunces", serif; font-weight: 800; font-size: 9.5px; line-height: 12px; }
</style>
</head>
<body>
<main class="canvas">

  <section class="panel front">
    <svg class="front-arc" width="574" height="430" viewBox="0 0 574 430" aria-hidden="true">
      <path d="M0 118 C70 70 130 50 160 0 L182 0 C150 62 80 100 0 150 Z" fill="#ff7212"/>
    </svg>
    <div class="brand-word">Herd Scan</div>
    <h1 class="headline">
      Affordable<br>
      Diagnostics<br>
      <span class="script">for</span><span class="accent">Healthy</span><br>
      <span class="accent indent">Herds</span>
    </h1>
    <p class="front-sub">Herd Scan Quick Assay<br>For Livestock</p>
    <div class="herd-photo" role="img" aria-label="Photo of a brown cow standing with a cream-coloured calf"></div>
  </section>

  <section class="panel side logo-panel">
    <div class="brand-word">Herd Scan</div>
  </section>

  <section class="panel side info-panel">
    <h2 class="info-title">Herd Scan<br>Quick Assay</h2>
    <p class="info-copy speed">Fast &amp; Efficient: Quick assay results in less than 10 minutes from prep to completion</p>
    <p class="info-copy note">Reliable &amp; Simple: Stable test performance with 2~30℃. Easy to operate, no professional skills required.</p>
    <div class="kid-photo" role="img" aria-label="Photo of a white young goat leaping"></div>
    <div class="value-box">
      <h3 class="value-title">Affordable:</h3>
      <p class="info-copy">Colloidal gold-based quick assays that combine high accuracy with cost effectiveness.</p>
      <div class="brand-word">Herd Scan</div>
    </div>
  </section>

  <section class="panel side spec-panel">
    <div class="spec">
      <p class="spec-name">HERD SCAN™</p>
      <p>Manufactured by AGRIVALE LABS</p>
      <p>Storage: 2-30°C, Do not freeze</p>
      <p>See the instructions for</p>
    </div>
  </section>

</main>
</body>
</html>
```